Website Redesign using existing images, copy etc.

I'm looking for a website redesign/refresh of my current WordPress website. I would like to utilize the same photography, a new photo viewer, and an overall refresh of the entire design. This will need to be WordPress with simple accessibility to make changes as we add additional properties and make updates. We auction luxury real estate and luxury yachts for non-distressed sellers. It needs to be simple, luxurious and with ease of use for both web and especially mobile. www.BrindleHarrow.com

```html
<!DOCTYPE html>
<html lang="en">
<head>
<meta charset="utf-8">
<title>Brindle Harrow — Real Estate &amp; Yachts</title>
<link rel="stylesheet" href="https://fonts.googleapis.com/css2?family=Jost:wght@300;400;500;600;700&family=Lato:wght@400;700&display=swap">
<style>
:root{
  --olive:#9a936b;
  --olive-dark:#8e8062;
  --olive-light:#a7a075;
  --btn:#a89e7a;
  --ink:#1f1f1f;
  --muted:#333;
  --white:#fff;
  --sea-top:#4d5a66;
  --sea-bot:#1f3a55;
}
*{margin:0;padding:0;box-sizing:border-box}
html,body{width:1200px;height:3134px;overflow:hidden;background:#fff}
body{position:relative;font-family:'Lato',sans-serif;color:var(--ink)}
.abs{position:absolute}
.heading{font-family:'Jost',sans-serif;font-weight:500;color:var(--ink)}
.pill{position:absolute;display:flex;align-items:center;border-radius:40px;background:var(--btn);color:#fff;font-family:'Jost',sans-serif;font-weight:600}
.pill .dot{width:38px;height:38px;border-radius:50%;border:2px solid #fff;margin:0 14px 0 4px;flex:none}

/* header */
.site-header{top:0;left:0;width:1200px;height:126px}
.brand{left:97px;top:27px;display:flex;align-items:center;gap:12px}
.brand .mark{width:75px;height:75px;border-radius:50%;border:2px solid var(--olive)}
.brand span{font-family:'Jost',sans-serif;font-weight:500;font-size:20px;color:var(--olive)}
.nav{top:56px;font-size:14px;letter-spacing:.5px;color:#333}
.phone{left:923px;top:37px;width:178px;height:55px;font-size:15px}
.phone .dot{width:44px;height:44px}

/* hero */
.hero{top:126px;left:0;width:1200px;height:614px}
.hero-text{left:96px;color:#fff}
.welcome{top:300px;font-family:'Jost',sans-serif;font-weight:300;font-size:27px}
.hero-title{top:350px;font-family:'Jost',sans-serif;font-weight:600;font-size:64px;letter-spacing:.5px}
.hero-sub{top:440px;font-family:'Jost',sans-serif;font-weight:300;font-size:22px}
.browse{left:97px;top:491px;width:259px;height:46px;font-size:12.5px}
.dots span{position:absolute;left:1139px;width:12px;height:12px;border-radius:50%;background:#fff}

/* intro */
.intro-title{left:617px;top:888px;font-size:40px;line-height:60px;width:480px}
.intro-text{left:617px;top:1043px;width:464px;font-size:16.5px;line-height:31px;text-align:justify;color:var(--muted)}

/* sold */
.sold{top:1388px;left:0;width:1200px;height:517px}
.sold-title{left:97px;top:1448px;font-size:38px;color:#fff}
.sold-text{left:97px;top:1527px;width:465px;font-size:14.5px;line-height:24.7px;color:#fff;text-align:justify}
.learn{left:97px;top:1800px;width:138px;height:46px;font-size:12px}

/* featured */
.featured-title{left:0;width:1200px;top:2010px;text-align:center;font-size:38px}
.press{top:2110px;width:117px;height:117px;border-radius:50%;border:2px solid var(--olive);display:flex;align-items:center;justify-content:center;text-align:center;font-family:'Jost',sans-serif;font-weight:600;font-size:13px;line-height:15px;color:#555;padding:10px}
.featured-text{left:150px;width:900px;top:2258px;text-align:center;font-size:15px;line-height:27px;color:var(--muted)}
.view{left:535px;top:2343px;width:130px;height:46px;font-size:12px}

/* promo band */
.promo-left{left:0;top:2506px;width:600px;height:224px;background:linear-gradient(90deg,#eceae6,#e4e1da)}
.promo-right{left:600px;top:2506px;width:600px;height:224px;background:linear-gradient(90deg,#a49c70,#988f66)}
.about-title{left:101px;top:2592px;font-size:40px}
.about-btn{left:300px;top:2597px;width:136px;height:46px;font-size:12px}
.upcoming{left:732px;top:2570px;font-size:40px;line-height:50px;color:#fff}
.browse2{left:967px;top:2597px;width:122px;height:46px;font-size:12px;background:#f3f2ee;color:#8a8466}
.browse2 .dot{border-color:#9a936b}

/* footer */
.foot-h{top:2840px;font-size:26px;font-weight:600}
.foot-h::after{content:"";display:block;width:42px;height:3px;background:var(--olive);margin-top:8px}
.links{left:104px;top:2903px;font-size:16px;line-height:22.5px;color:#333;list-style:none}
.news-text{left:443px;top:2903px;width:300px;font-size:15.5px;line-height:22.5px;color:#333}
.email{left:440px;top:2962px;width:373px;height:46px;border:1px solid #9a936b;border-radius:30px}
.email span{position:absolute;left:20px;top:13px;font-size:15px;color:#555}
.subscribe{left:675px;top:2966px;width:131px;height:38px;justify-content:center;font-size:16px}
.social{top:2906px;width:38px;height:38px;border-radius:50%;border:1.5px solid var(--olive)}
.legal{left:885px;top:2958px;font-size:15px;line-height:22.5px;color:#222;list-style:none}
.copy{left:0;width:1200px;top:3078px;text-align:center;font-size:14.5px;color:#333}
.badge{left:1046px;top:3047px;width:50px;height:50px;border-radius:50%;background:#8a8466}
</style>
</head>
<body>

<header class="site-header abs">
  <div class="brand abs"><div class="mark"></div><span>Brindle Harrow</span></div>
  <nav>
    <span class="nav abs" style="left:528px">BUY</span>
    <span class="nav abs" style="left:609px">SELL</span>
    <span class="nav abs" style="left:695px">ABOUT</span>
    <span class="nav abs" style="left:797px">CONTACT</span>
  </nav>
  <div class="pill phone"><span class="dot"></span>800-555-0147</div>
</header>

<section class="hero abs">
  <svg width="1200" height="614" viewBox="0 0 1200 614" style="position:absolute;left:0;top:0">
    <defs>
      <linearGradient id="sea" x1="0" y1="0" x2="0" y2="1">
        <stop offset="0" stop-color="#58606a"/>
        <stop offset=".35" stop-color="#3d4f45"/>
        <stop offset="1" stop-color="#1c3957"/>
      </linearGradient>
    </defs>
    <polygon points="0,0 1200,0 1200,536 988,600 0,530" fill="url(#sea)" role="img" aria-label="Aerial photograph of a waterfront estate on a wooded peninsula"/>
    <polygon points="0,530 988,600 1200,536 1200,547 988,614 0,540" fill="var(--olive)"/>
  </svg>
</section>
<div class="hero-text abs welcome">WELCOME TO</div>
<div class="hero-text abs hero-title">BRINDLE HARROW</div>
<div class="hero-text abs hero-sub">REAL ESTATE &amp; YACHTS</div>
<div class="pill browse"><span class="dot"></span>BROWSE UPCOMING AUCTIONS</div>
<div class="dots">
  <span style="top:389px"></span>
  <span style="top:407px"></span>
  <span style="top:426px;background:var(--olive)"></span>
  <span style="top:445px"></span>
</div>

<svg class="abs" style="left:100px;top:840px" width="430" height="435" viewBox="0 0 430 435">
  <polyline points="9,415 9,140 405,6 405,16" fill="none" stroke="var(--olive)" stroke-width="3"/>
  <polygon points="19,148 417,18 417,428 19,428" fill="#3a5a82" role="img" aria-label="Photograph of a luxury motor yacht on the water"/>
</svg>
<h2 class="heading abs intro-title">Over One Billion Dollars of Auctions Marketed</h2>
<p class="abs intro-text">The experience of hearing the auctioneer’s final proclamation of “SOLD!” is unparalleled. Whether it’s the initial meeting with the seller at their estate or yacht, or the triumphant raising of the paddle by the winning buyer, we relish every moment of the process and the ensuing festivities. We’re confident that you will, too.</p>

<section class="sold abs">
  <svg width="1200" height="517" viewBox="0 0 1200 517" style="position:absolute;left:0;top:0">
    <rect width="1200" height="517" fill="var(--olive-dark)"/>
    <polygon points="555,0 1200,0 1200,517 700,517" fill="var(--olive-light)"/>
    <polygon points="572,0 1200,0 1200,517 716,517" fill="#9c7e6e" role="img" aria-label="Photograph of a Mediterranean style estate with palm trees at dusk"/>
  </svg>
</section>
<h2 class="heading abs sold-title">Sold by Brindle Harrow</h2>
<p class="abs sold-text">Brindle Harrow is a top-tier destination for luxury property auctions, having overseen the auction marketing of numerous high-end estates and yachts. Our team of luxury home auction experts is committed to helping property owners obtain the best value for their assets while ensuring a timely sale. Whether you have an expansive compound or a metropolitan penthouse, Brindle Harrow has the necessary skills and expertise to facilitate various luxury real estate auctions. What’s even better? Our team takes care of every aspect of the process in cooperation with tour realtor/broker, including property tours, photography and cinematography, marketing advertising,</p>
<div class="pill learn"><span class="dot"></span>Learn More</div>

<h2 class="heading abs featured-title">As Featured In</h2>
<div class="press abs" style="left:181px">Channel Meridian</div>
<div class="press abs" style="left:361px">Meridian Business</div>
<div class="press abs" style="left:541px">Estate Ledger</div>
<div class="press abs" style="left:721px">The Market Journal</div>
<div class="press abs" style="left:901px">Capitalis</div>
<p class="abs featured-text">By offering top-tier properties and vessels globally, along with strategic auction dates, exceptional marketing tactics, and a diligent public relations team, even the most prominent media outlets have taken notice. Check out some of our latest press features.</p>
<div class="pill view"><span class="dot"></span>View Press</div>

<div class="abs promo-left" role="img" aria-label="Faded photograph of an estate facade"></div>
<div class="abs promo-right" role="img" aria-label="Olive tinted photograph of an estate facade"></div>
<h2 class="heading abs about-title">About us</h2>
<div class="pill about-btn"><span class="dot"></span>Learn More</div>
<h2 class="heading abs upcoming">Upcoming<br>Auctions</h2>
<div class="pill browse2"><span class="dot"></span>Browse</div>

<footer>
  <h3 class="heading abs foot-h" style="left:101px">Quick Links</h3>
  <ul class="abs links"><li>Home</li><li>Buy</li><li>Sell</li><li>About</li><li>Blog</li><li>Contact</li></ul>

  <h3 class="heading abs foot-h" style="left:440px">Subscribe to Newsletter</h3>
  <p class="abs news-text">Lorem ipsum dolor sit amet, consectetur adipiscing</p>
  <div class="abs email"><span>Email*</span></div>
  <div class="pill subscribe">Subscribe</div>

  <h3 class="heading abs foot-h" style="left:882px">Follow Us</h3>
  <span class="abs social" style="left:884px" aria-label="Social profile one"></span>
  <span class="abs social" style="left:928px" aria-label="Social profile two"></span>
  <span class="abs social" style="left:972px" aria-label="Social profile three"></span>
  <span class="abs social" style="left:1016px" aria-label="Social profile four"></span>
  <ul class="abs legal"><li>Terms Of Service</li><li>Copyright Policy</li><li>Privacy Policy</li></ul>

  <p class="abs copy">©Copyrights 2023 BrindleHarrow &nbsp;|&nbsp;&nbsp; All Rights Reserved</p>
  <div class="abs badge" aria-label="Owned business badge"></div>
</footer>

</body>
</html>
```